Marlow Sail Works President Business Card Carbon fiber catamarans

Hi.. I need a new business card design.. I am the President of a high tech yacht builder. We build Carbon Fiber go fast catamarans... Maybe we use the file I am sharing to you as the back of the card.. We need to look cool and crisp ...

Target Market(s)

Affluent People who will purchase a cool yacht

Industry/Entity Type

Custom Yacht Builder

Contact Information for Business Card

Dean Pellway , President, 731.508.2164 USA

Font styles to use
Serif

Requirements
Must have
• the clean crisp cool feel
Nice to have
• clean and crisp
Should not have
• Bold ugly

```html
<!DOCTYPE html>
<html lang="en">
<head>
<meta charset="utf-8">
<title>Marlow Sail Works – Business Card</title>
<link rel="stylesheet" href="https://fonts.googleapis.com/css2?family=Michroma&family=Nunito+Sans:wght@400&display=swap">
<style>
  :root{
    --backdrop:#1c1c1c;
    --card:#0b0b0b;
    --silver:#d9d9d9;
    --silver-dim:#a9a9a9;
    --text:#e8e8e8;
    --rule:#2e2e2e;
  }
  *{margin:0;padding:0;box-sizing:border-box;}
  html,body{width:1200px;height:900px;overflow:hidden;background:var(--backdrop);}
  .sheet{width:1200px;height:900px;display:flex;align-items:center;justify-content:center;gap:40px;}
  .card{width:540px;height:310px;background:var(--card);border-radius:18px;position:relative;
        box-shadow:0 12px 30px rgba(0,0,0,.55);color:var(--text);}
  .brand{display:flex;align-items:center;gap:12px;}
  .brand-dot{width:26px;height:26px;border-radius:50%;background:var(--silver);flex:none;}
  .brand-name{font-family:"Michroma",sans-serif;color:var(--silver);letter-spacing:.12em;
              text-transform:uppercase;line-height:1.35;}

  /* front */
  .card-front .brand{position:absolute;left:34px;top:134px;}
  .card-front .brand-name{font-size:15px;width:200px;}
  .divider{position:absolute;left:282px;top:44px;width:1px;height:222px;background:var(--rule);}
  .contact{position:absolute;left:306px;top:62px;font-family:"Nunito Sans",sans-serif;}
  .person-name{font-family:"Michroma",sans-serif;font-size:15px;letter-spacing:.14em;
               text-transform:uppercase;color:var(--silver);}
  .person-title{font-size:13px;color:var(--text);margin-top:4px;}
  .contact-list{list-style:none;margin-top:18px;}
  .contact-list li{display:flex;align-items:center;gap:9px;font-size:13px;margin-bottom:6px;}
  .contact-list svg{width:13px;height:13px;fill:var(--silver-dim);flex:none;}
  .contact-list .address{margin-top:18px;}

  /* back */
  .card-back{display:flex;align-items:center;justify-content:center;}
  .card-back .brand{gap:18px;}
  .card-back .brand-dot{width:44px;height:44px;}
  .card-back .brand-name{font-size:26px;}
</style>
</head>
<body>
<main class="sheet">
  <section class="card card-front" aria-label="Card front">
    <div class="brand">
      <span class="brand-dot"></span>
      <span class="brand-name">Marlow Sail Works</span>
    </div>
    <div class="divider"></div>
    <div class="contact">
      <p class="person-name">Dean Pellway</p>
      <p class="person-title">President</p>
      <ul class="contact-list">
        <li><svg viewBox="0 0 24 24"><path d="M6.6 10.8a15 15 0 0 0 6.6 6.6l2.2-2.2c.3-.3.7-.4 1-.2 1.1.4 2.3.6 3.6.6.6 0 1 .4 1 1V20c0 .6-.4 1-1 1A17 17 0 0 1 3 4c0-.6.4-1 1-1h3.5c.6 0 1 .4 1 1 0 1.3.2 2.5.6 3.6.1.3 0 .7-.2 1z"/></svg>731.508.2164</li>
        <li><svg viewBox="0 0 24 24"><path d="M2 5h20v14H2zm2 2v.5l8 5 8-5V7zm0 2.8V17h16V9.8l-8 5z"/></svg>info@marlowsail.com</li>
        <li><svg viewBox="0 0 24 24"><path d="M12 2a10 10 0 1 0 0 20 10 10 0 0 0 0-20zm6.9 9h-3a15 15 0 0 0-1.3-6 8 8 0 0 1 4.3 6zM12 4.1c.9 1.3 1.7 3.6 1.9 6.9h-3.8c.2-3.3 1-5.6 1.9-6.9zM9.4 5a15 15 0 0 0-1.3 6h-3a8 8 0 0 1 4.3-6zM5.1 13h3a15 15 0 0 0 1.3 6 8 8 0 0 1-4.3-6zm6.9 6.9c-.9-1.3-1.7-3.6-1.9-6.9h3.8c-.2 3.3-1 5.6-1.9 6.9zm2.6-.9a15 15 0 0 0 1.3-6h3a8 8 0 0 1-4.3 6z"/></svg>www.marlowsailworks.com</li>
        <li class="address"><svg viewBox="0 0 24 24"><path d="M12 2a7 7 0 0 0-7 7c0 5 7 13 7 13s7-8 7-13a7 7 0 0 0-7-7zm0 9.5A2.5 2.5 0 1 1 12 6.5a2.5 2.5 0 0 1 0 5z"/></svg>Tennessee 38301, USA</li>
      </ul>
    </div>
  </section>

  <section class="card card-back" aria-label="Card back">
    <div class="brand">
      <span class="brand-dot"></span>
      <span class="brand-name">Marlow<br>Sail Works</span>
    </div>
  </section>
</main>
</body>
</html>
```